Beauty Therapy Web Design

I need a web page design for a small beauty therapy clinic, the owner is currently the only beauty therapist working there.
We require the following pages:
Home
About
Treatments
Nails
Courses
Contact
I will attach the clinics business card, treatment menu and signage so that you get a feeling for the branding colours etc.
This is the first website for the beauty therapist, she would like to attract new clients and also tourists that come in on the cruise ships. The thing that sets her apart from other clinics is that she welcomes texting for appointments.
I have selected refundable because I have never done this before so I don't know what to expect, I have the full intention of going through with it as long as I get a good design.
Feel free to ask for further information
Reason: Project extended as I am away for work and am unable to meet with the owner.
Target Market(s)
Females 18 to 50
Industry/Entity Type
Business
Look and feel

```html
<!DOCTYPE html>
<html lang="en">
<head>
<meta charset="utf-8">
<title>Lumiera Beauty Therapy</title>
<link rel="stylesheet" href="https://fonts.googleapis.com/css2?family=Poiret+One&family=Parisienne&family=Dancing+Script:wght@500&family=Tinos:ital@1&family=Arimo&display=swap">
<style>
:root{
  --purple:#93139f;
  --purple-deep:#7d0a8a;
  --footer:#a607b8;
  --pink:#e444ee;
  --pink-dark:#c52bd2;
  --yellow:#ffee00;
  --white:#ffffff;
  --ink:#111111;
  --frame:#6b4a1a;
  --caption:rgba(30,30,30,.85);
}
*{margin:0;padding:0;box-sizing:border-box}
html,body{width:1200px;height:900px;overflow:hidden;background:var(--white)}
body{position:relative;font-family:"Tinos",serif}
.abs{position:absolute}

.site-header{left:0;top:0;width:1200px;height:151px;
  background:linear-gradient(180deg,#9a1ba6 0%,var(--purple) 60%,var(--purple-deep) 100%);
  box-shadow:0 2px 3px rgba(0,0,0,.45)}
.brand-name{left:50px;top:70px;font-family:"Poiret One",sans-serif;font-size:50px;font-weight:400;color:var(--yellow);letter-spacing:1px}
.brand-tagline{left:254px;top:46px;font-family:"Poiret One",sans-serif;font-size:30px;color:var(--white);letter-spacing:.5px}
.phones{right:50px;top:6px;text-align:right;font-family:"Tinos",serif;font-style:italic;font-size:24px;line-height:30px;color:var(--white);letter-spacing:2px}

.main-nav{left:528px;top:97px;width:621px;height:52px;background:var(--pink);border-radius:8px 8px 4px 4px;
  display:flex;align-items:center;justify-content:center;gap:0}
.nav-link,.footer-link{font-family:"Parisienne",cursive;font-size:23px;color:var(--white);text-decoration:none;
  text-shadow:1px 2px 2px rgba(0,0,0,.6);padding:0 10px}
.nav-sep{color:var(--white);font-family:"Arimo",sans-serif;font-size:22px}

.gallery{left:50px;top:168px;width:1101px;height:340px;border:2px solid var(--frame);border-radius:8px}
.tile{top:184px;height:311px;box-shadow:1px 2px 3px rgba(0,0,0,.35)}
.tile-caption{left:0;right:0;top:250px;height:46px;background:var(--caption);
  color:var(--white);font-family:"Poiret One",sans-serif;font-size:32px;text-align:center;line-height:46px}

.services-btn{left:51px;top:525px;width:249px;height:65px;background:var(--pink);border-radius:7px;
  box-shadow:1px 2px 3px rgba(0,0,0,.4);font-family:"Poiret One",sans-serif;font-size:36px;color:var(--white);
  line-height:65px;padding-left:26px;text-shadow:1px 1px 1px rgba(0,0,0,.6)}
.services-list{left:58px;top:613px;list-style:none;font-family:"Tinos",serif;font-style:italic;font-size:24px;line-height:29px;color:var(--ink)}
.more-btn{left:191px;top:760px;width:141px;height:44px;background:var(--pink);border-radius:5px;
  box-shadow:1px 2px 3px rgba(0,0,0,.4);font-family:"Poiret One",sans-serif;font-size:22px;color:var(--white);
  text-align:center;line-height:46px;letter-spacing:1px}
.divider{width:2px;background:#333}
.welcome-title{left:370px;top:544px;font-family:"Parisienne",cursive;font-size:38px;color:var(--ink);letter-spacing:1px}
.welcome-text{left:380px;top:613px;width:400px;font-family:"Dancing Script",cursive;font-size:27px;line-height:29px;letter-spacing:2.5px;color:var(--ink)}
.welcome-sign{left:640px;top:758px;font-family:"Parisienne",cursive;font-size:46px;color:#a010b0;letter-spacing:2px}
.massage-photo{left:872px;top:524px;width:279px;height:223px}
.massage-caption{right:50px;top:760px;font-family:"Poiret One",sans-serif;font-size:22px;letter-spacing:2px;color:var(--ink)}

.site-footer{left:0;top:825px;width:1200px;height:69px;background:var(--footer)}
.copyright{left:52px;top:853px;font-family:"Arimo",sans-serif;font-size:17px;color:var(--white)}
.footer-nav{right:40px;top:842px;display:flex;align-items:center}
</style>
</head>
<body>
<header class="site-header abs"></header>
<div class="brand-tagline abs">BEAUTY THREAPY</div>
<div class="brand-name abs">Lumiera</div>
<div class="phones abs">021-555-0147<br>07-555-0182</div>
<nav class="main-nav abs">
  <a class="nav-link" href="#">Home</a><span class="nav-sep">|</span>
  <a class="nav-link" href="#">Treatments</a><span class="nav-sep">|</span>
  <a class="nav-link" href="#">Courses</a><span class="nav-sep">|</span>
  <a class="nav-link" href="#">About Us</a><span class="nav-sep">|</span>
  <a class="nav-link" href="#">Contact Us</a>
</nav>

<section class="gallery abs"></section>
<div class="tile abs" role="img" aria-label="Spray tan treatment photo" style="left:60px;width:231px;background:linear-gradient(90deg,#c99a78,#f1d9c6)">
  <div class="tile-caption abs">SPRAY TANS</div></div>
<div class="tile abs" role="img" aria-label="Eye lash styling photo" style="left:300px;width:250px;background:linear-gradient(135deg,#e6c8b0,#c89a80)">
  <div class="tile-caption abs">EYE LASH</div></div>
<div class="tile abs" role="img" aria-label="Manicure and pedicure photo" style="left:560px;width:241px;background:linear-gradient(180deg,#e8c9a8,#f4dcc0)">
  <div class="tile-caption abs">MANICURES</div></div>
<div class="tile abs" role="img" aria-label="Gel nails photo" style="left:811px;width:230px;background:linear-gradient(135deg,#f2eef2,#dcc7cf)">
  <div class="tile-caption abs">GEL NAILS</div></div>
<div class="abs" role="img" aria-label="Skin care photo with lily" style="left:1041px;top:202px;width:100px;height:265px;background:linear-gradient(180deg,#f1ded6,#f3c9d2);box-shadow:1px 2px 3px rgba(0,0,0,.35)"></div>

<div class="services-btn abs">OUR SERVICES</div>
<ul class="services-list abs">
  <li>Face Facial</li><li>Spray Tans</li><li>Eye Lash</li><li>Pedicures</li><li>Manicures</li><li>Gel Nails</li>
</ul>
<div class="more-btn abs">MORE &gt;&gt;&gt;</div>
<div class="divider abs" style="left:346px;top:600px;height:190px"></div>
<div class="divider abs" style="left:852px;top:600px;height:186px"></div>

<h1 class="welcome-title abs" style="font-weight:400">Welcome to Our Website</h1>
<p class="welcome-text abs">Its a Short paragraph in which given detail about Owner and centre where you doing these services.</p>
<div class="welcome-sign abs">Lumiera</div>

<div class="massage-photo abs" role="img" aria-label="Massage service photo" style="background:linear-gradient(135deg,#ece6e2,#c79478 60%,#efe9e6)"></div>
<div class="massage-caption abs">MASSAGE SERVICE</div>

<footer class="site-footer abs"></footer>
<div class="copyright abs">Copyright © Nova Page Studio 2012</div>
<nav class="footer-nav abs">
  <a class="footer-link" href="#">Home</a><span class="nav-sep">|</span>
  <a class="footer-link" href="#">Treatments</a><span class="nav-sep">|</span>
  <a class="footer-link" href="#">Courses</a><span class="nav-sep">|</span>
  <a class="footer-link" href="#">About Us</a><span class="nav-sep">|</span>
  <a class="footer-link" href="#">Contact Us</a>
</nav>
</body>
</html>
```